Label Craft Beer with CBD

Create a label for our cbd (cannabidiol) beer. We do have a first / simple idea. now it needs a professional finish. Please show your very own idea as well, because ours is only a draft and we need YOUR HELP! size front: H 8 cm, W 7 cm size back: H 7.5 cm, W 5.5 cm

```html
<!DOCTYPE html>
<html lang="en">
<head>
<meta charset="utf-8">
<title>Verda Brew – Premium Lager Label</title>
<link href="https://fonts.googleapis.com/css2?family=Montserrat:wght@300;400;700;800&family=Raleway:wght@200;300&display=swap" rel="stylesheet">
<style>
  :root {
    --page: #efefef;
    --label: #0a1015;
    --white: #ffffff;
    --muted: #b9c0c4;
    --rule: #6f787d;
    --teal: #4cc7bd;
    --teal-bright: #5fe0d4;
    --leaf-light: #a6e8c8;
    --leaf-mid: #58c08a;
    --leaf-dark: #1f7a4c;
  }
  * { margin: 0; padding: 0; box-sizing: border-box; }
  html, body {
    width: 1200px; height: 848px; overflow: hidden;
    background: var(--page);
    font-family: "Montserrat", Arial, sans-serif;
  }
  .front-label {
    position: absolute; left: 320px; top: 104px;
    width: 560px; height: 640px;
    background: var(--label);
    color: var(--white);
  }
  .brewery-mark {
    position: absolute; left: 0; right: 0; top: 56px;
    display: flex; justify-content: center; align-items: center; gap: 10px;
  }
  .brewery-mark .dot {
    width: 18px; height: 18px; border-radius: 50%;
    border: 2px solid var(--white);
  }
  .brewery-mark .name {
    font-weight: 700; font-size: 17px; letter-spacing: 4px; color: var(--white);
  }
  .origin-badge {
    position: absolute; left: 462px; top: 6px;
    display: flex; flex-direction: column; align-items: flex-start; gap: 6px;
  }
  .origin-badge .square { width: 30px; height: 30px; background: var(--white); }
  .origin-badge .text {
    font-size: 10px; font-weight: 400; line-height: 1.25; color: var(--white);
  }
  .product-name {
    position: absolute; left: 0; right: 0; top: 136px;
    text-align: center;
    font-weight: 800; font-size: 54px; letter-spacing: 2px; line-height: 1;
  }
  .illustration {
    position: absolute; left: 175px; top: 200px;
    width: 230px; height: 270px;
  }
  .volume {
    position: absolute; left: 64px; top: 460px;
    font-family: "Raleway", Arial, sans-serif;
    font-weight: 300; font-size: 19px; color: var(--muted);
  }
  .info-box {
    position: absolute; left: 61px; top: 491px;
    width: 436px; height: 110px;
    border: 1px solid var(--rule);
    text-align: center;
  }
  .style-name {
    font-family: "Raleway", Arial, sans-serif;
    font-weight: 300; font-size: 40px; letter-spacing: 1px;
    color: var(--muted);
    margin: 12px auto 0; width: 380px;
    padding-bottom: 6px;
    border-bottom: 2px solid var(--muted);
    line-height: 1.1;
  }
  .facts {
    display: flex; justify-content: center; align-items: center; gap: 10px;
    margin-top: 10px;
    font-size: 15px; font-weight: 400; letter-spacing: 0.5px; color: var(--teal);
  }
  .facts .sep { width: 2px; height: 22px; background: var(--muted); }
  .facts .highlight { font-weight: 700; color: var(--teal-bright); }
</style>
</head>
<body>
  <main class="front-label">
    <div class="brewery-mark">
      <span class="dot"></span>
      <span class="name">ALPENFINK</span>
    </div>

    <div class="origin-badge">
      <span class="square"></span>
      <span class="text">SWISS<br>MADE</span>
    </div>

    <h1 class="product-name">VERDA BREW</h1>

    <svg class="illustration" viewBox="0 0 230 270" role="img"
         aria-label="Illustration of a head in profile filled with green hemp leaves">
      <defs>
        <linearGradient id="leafFill" x1="0" y1="0" x2="1" y2="1">
          <stop offset="0" stop-color="var(--leaf-light)"/>
          <stop offset="0.55" stop-color="var(--leaf-mid)"/>
          <stop offset="1" stop-color="var(--leaf-dark)"/>
        </linearGradient>
      </defs>
      <ellipse cx="115" cy="135" rx="110" ry="132" fill="url(#leafFill)"/>
    </svg>

    <p class="volume">330CL</p>

    <section class="info-box">
      <h2 class="style-name">PREMIUM LAGER</h2>
      <div class="facts">
        <span>NATURTRUB</span>
        <span class="sep"></span>
        <span class="highlight">10 MG CBD</span>
        <span class="sep"></span>
        <span>4.3% ALC</span>
      </div>
    </section>
  </main>
</body>
</html>
```